TL - business card

Tallow Partners is an insurance brokerage firm, inovative, proactive, vigorous, which aims to become the leader of the insurance brokers in Anfrica. We should like to get some designs which should be avoided also in Gray / Metallic for the Administration and Orange / Blue for the Managers (ike in the picture sent). The Blue / Green logo is not the correct one, but the source of the file. Please adjust the color accordingly for the business cards. 1 / Orange / Blue 2 / Gray / Metallic We want something classic but which is transmitted strenght, inovation, modernity and most of all, rapidity. We want something start-up like, very punchy and catching eye remaining profesional at the same time. Name: Dorian Whitlock Function: Managing Director Address: N ° 17/18 Rua Veloso - R / C 2B Direita - Bairro Mutamba - Luanda Tel: (+244) 947 582 316 Email: dorian.whitlock@tallow-p.example Website: www.tallow-p. example We want classic in the front and creative, colorfull at the back. The cards will be printed in relief, with very high quality of paper.
Insurance Broker
Colors
Designer to choose colors to be used in the design.

```html
<!DOCTYPE html>
<html lang="en">
<head>
<meta charset="utf-8">
<title>Tallow Partners – Business Card</title>
<link rel="stylesheet" href="https://fonts.googleapis.com/css2?family=Open+Sans:wght@400;600;700&display=swap">
<style>
  :root {
    --backdrop: #e6e1da;
    --card: #f4f4f2;
    --card-edge: #dcdcd8;
    --brand-orange: #ef7d1a;
    --brand-blue: #1f6fa8;
    --text-grey: #7a7a78;
  }
  * { margin: 0; padding: 0; box-sizing: border-box; }
  html, body {
    width: 1200px; height: 1047px; overflow: hidden;
    background: var(--backdrop);
    font-family: "Open Sans", Arial, sans-serif;
  }
  .business-card {
    position: absolute; left: 151px; top: 289px;
    width: 945px; height: 516px;
    background: var(--card);
    border: 1px solid var(--card-edge);
    border-radius: 22px;
    overflow: hidden;
    box-shadow: 0 10px 30px rgba(0,0,0,0.08);
  }
  .accent-band {
    position: absolute; top: 0; right: 0;
    width: 270px; height: 100%;
    background: var(--brand-orange);
  }
  .company-name {
    position: absolute; left: 39px; top: 29px;
    font-size: 34px; line-height: 46px; font-weight: 700; letter-spacing: 0.5px;
    color: var(--brand-blue);
    text-transform: uppercase;
  }
  .person-name {
    position: absolute; left: 39px; top: 146px;
    font-size: 35px; line-height: 46px; font-weight: 600; letter-spacing: 0.5px;
    color: var(--brand-blue);
  }
  .person-role {
    position: absolute; left: 39px; top: 190px;
    font-size: 20px; line-height: 29px; color: var(--text-grey);
  }
  .address {
    position: absolute; left: 39px; top: 273px;
    font-size: 20px; line-height: 29px; color: var(--text-grey);
    font-style: normal;
  }
  .contact-list { position: absolute; left: 39px; top: 404px; list-style: none; }
  .contact-item {
    display: flex; align-items: center; gap: 13px;
    font-size: 20px; line-height: 29px; color: var(--text-grey);
  }
  .contact-icon { width: 16px; height: 16px; flex: none; }
</style>
</head>
<body>
  <section class="business-card">
    <div class="company-name">Tallow-Partners</div>
    <h1 class="person-name">Dorian Whitlock</h1>
    <p class="person-role">Managing Director</p>
    <address class="address">
      N ° 17/18 Rua Veloso<br>
      R / C 2B Direita<br>
      Bairro Mutamba - Luanda
    </address>
    <ul class="contact-list">
      <li class="contact-item">
        <svg class="contact-icon" viewBox="0 0 16 16" aria-hidden="true">
          <path d="M3.5 1.5l2.5 0.5 1 3-1.6 1.2a8 8 0 0 0 4.4 4.4L11 9l3 1 0.5 2.5-1.8 1.8C7 14 2 9 1.7 3.3z" fill="var(--brand-orange)"/>
        </svg>
        <span>+244 947 582 316</span>
      </li>
      <li class="contact-item">
        <svg class="contact-icon" viewBox="0 0 16 16" aria-hidden="true">
          <rect x="1.5" y="3.5" width="13" height="9" rx="1" fill="none" stroke="var(--brand-orange)" stroke-width="1.6"/>
          <path d="M2 4.5l6 4.5 6-4.5" fill="none" stroke="var(--brand-orange)" stroke-width="1.6"/>
        </svg>
        <span>dorian.whitlock@tallow-p.example</span>
      </li>
      <li class="contact-item">
        <svg class="contact-icon" viewBox="0 0 16 16" aria-hidden="true">
          <circle cx="8" cy="8" r="6.5" fill="none" stroke="var(--brand-orange)" stroke-width="1.5"/>
          <ellipse cx="8" cy="8" rx="2.8" ry="6.5" fill="none" stroke="var(--brand-orange)" stroke-width="1.3"/>
          <path d="M1.5 8h13" stroke="var(--brand-orange)" stroke-width="1.3"/>
        </svg>
        <span>www.tallow-p. example</span>
      </li>
    </ul>
    <div class="accent-band"></div>
  </section>
</body>
</html>
```